Animal Eye Clinic needs a Business card

We are a new veterinary ophthalmology practice (Ridgeline Pet Vision Care) and we need a business card designed. We only see animal eyes - we are not a regular veterinary clinic. We already have a logo. We are looking for a professional, good looking business card to hand out to our clients. We are looking for something simple but professional and contemporary. Our logo is likely the only picture/graphic that needs to be on the card.
Updates

Contact Information for Business Card

Delia Vossman, BSc, DVM, MSc, DipACVO
Veterinary Ophthalmologist

Phone: 250.418.3927
Email: ridgelinepetvisioncare@mailbox-example.net
Website: ridgelinepetvisioncare-example.net
Address: 1874 Thornbury Rd
Kelowna, BC, V1X 4M9

Colors

Designer to choose colors to be used in the design.

Requirements
Must have
• Our logo (attached)

```html
<!DOCTYPE html>
<html lang="en">
<head>
<meta charset="utf-8">
<title>Ridgeline Pet Vision Care — Business Card</title>
<link rel="stylesheet" href="https://fonts.googleapis.com/css2?family=Montserrat:wght@700&family=Roboto:wght@300;400;500&display=swap">
<style>
  :root {
    --teal: #0e8fa0;
    --teal-soft: rgba(14, 143, 160, 0.35);
    --grey-soft: rgba(111, 111, 111, 0.25);
    --paper: #fbfbfb;
    --slate: #4a4b4d;
    --slate-light: #55565a;
    --white: #ffffff;
    --backdrop: #d9dadc;
  }
  * { box-sizing: border-box; margin: 0; padding: 0; }
  html, body { width: 1200px; height: 1125px; overflow: hidden; }
  body {
    background: var(--backdrop);
    font-family: "Roboto", Arial, sans-serif;
    position: relative;
  }
  .card {
    position: absolute;
    left: 150px;
    width: 900px;
    height: 514px;
    border-bottom: 6px solid var(--teal);
    overflow: hidden;
  }

  /* Shared wordmark: one colour, one weight */
  .wordmark {
    color: var(--teal);
    font-weight: 500;
    text-transform: uppercase;
    line-height: 1.15;
  }
  .wordmark-top { display: block; letter-spacing: 0.62em; }
  .wordmark-main { display: block; letter-spacing: 0.02em; }

  /* Front side */
  .card-front { top: 30px; background: var(--paper); }
  .front-emblem {
    position: absolute;
    left: 40px; top: 40px;
    width: 470px; height: 470px;
    border-radius: 50%;
    background: radial-gradient(circle at 45% 45%, var(--teal-soft) 0%, var(--grey-soft) 55%, rgba(251,251,251,0) 72%);
  }
  .front-wordmark {
    position: absolute;
    left: 545px; top: 200px;
  }
  .front-wordmark .wordmark-top { font-size: 20px; }
  .front-wordmark .wordmark-main { font-size: 36px; margin-top: 4px; }

  /* Back side */
  .card-back { top: 581px; background: var(--slate); color: var(--white); }
  .back-decoration {
    position: absolute;
    right: -60px; top: 30px;
    width: 500px; height: 500px;
    border-radius: 50%;
    background: radial-gradient(circle at 45% 40%, var(--slate-light), rgba(74,75,77,0) 70%);
  }
  .back-wordmark {
    position: absolute;
    left: 60px; top: 40px;
    display: flex; align-items: center; gap: 14px;
  }
  .brand-dot { width: 46px; height: 46px; border-radius: 50%; background: var(--teal); flex: none; }
  .back-wordmark .wordmark-top { font-size: 15px; }
  .back-wordmark .wordmark-main { font-size: 27px; margin-top: 2px; }

  .contact-block { position: absolute; left: 60px; top: 128px; }
  .person-name {
    font-family: "Montserrat", Arial, sans-serif;
    font-weight: 700;
    font-size: 26px;
    letter-spacing: 0.14em;
    color: var(--teal);
    text-transform: uppercase;
    display: flex; align-items: center; gap: 12px;
  }
  .person-name svg { width: 22px; height: 22px; }
  .credentials { color: var(--teal); font-size: 19px; font-weight: 300; margin: 4px 0 0 34px; }
  .role { font-size: 20px; margin: 2px 0 0 34px; }
  .address { font-size: 20px; line-height: 1.3; margin: 28px 0 0 34px; }
  .contact-list { list-style: none; margin: 20px 0 0 34px; font-size: 20px; line-height: 1.4; }
  .contact-list li { display: flex; align-items: center; gap: 8px; }
  .contact-list svg { width: 16px; height: 16px; fill: var(--teal); flex: none; }
</style>
</head>
<body>
  <section class="card card-front">
    <div class="front-emblem" role="img" aria-label="Brand illustration area"></div>
    <div class="front-wordmark wordmark">
      <span class="wordmark-top">Ridgeline</span>
      <span class="wordmark-main">Pet Vision Care</span>
    </div>
  </section>

  <section class="card card-back">
    <div class="back-decoration" role="img" aria-label="Faint embossed brand illustration area"></div>
    <div class="back-wordmark">
      <span class="brand-dot" aria-hidden="true"></span>
      <div class="wordmark">
        <span class="wordmark-top">Ridgeline</span>
        <span class="wordmark-main">Pet Vision Care</span>
      </div>
    </div>
    <div class="contact-block">
      <h1 class="person-name">
        <svg viewBox="0 0 20 20" aria-hidden="true"><polygon points="2,2 18,10 2,18" fill="var(--teal)"/></svg>
        Delia Vossman
      </h1>
      <p class="credentials">BSc, DVM, MSc, DipACVO</p>
      <p class="role">Veterinary Ophthalmologist</p>
      <p class="address">1874 Thornbury Rd<br>Kelowna, BC, V1X 4M9</p>
      <ul class="contact-list">
        <li><svg viewBox="0 0 24 24" aria-hidden="true"><path d="M6.6 10.8a15 15 0 0 0 6.6 6.6l2.2-2.2a1 1 0 0 1 1-.25 11.4 11.4 0 0 0 3.6.57 1 1 0 0 1 1 1V20a1 1 0 0 1-1 1A17 17 0 0 1 3 4a1 1 0 0 1 1-1h3.5a1 1 0 0 1 1 1c0 1.25.2 2.45.57 3.57a1 1 0 0 1-.25 1z"/></svg>250.418.3927</li>
        <li><svg viewBox="0 0 24 24" aria-hidden="true"><path d="M2 5h20v14H2z M2 5l10 8 10-8" stroke="var(--slate)" stroke-width="1.5"/></svg>ridgelinepetvisioncare@mailbox-example.net</li>
        <li><svg viewBox="0 0 24 24" aria-hidden="true"><circle cx="12" cy="12" r="10"/></svg>ridgelinepetvisioncare-example.net</li>
      </ul>
    </div>
  </section>
</body>
</html>
```